Business card for Crestline Bathrooms

Please design a business card for our bathroom renovation business. You can use my existing logo, but if you have an idea to modernize it, I would like to see it. Please see attached files first. I would like to use the blue and the orange theme. I like the concept of using the shower head in the logo. Please find following a design (or two) that I have been trying to create with my limited resources. That design was for a sign, but I was going to adopt it and use it as a business card as well. I like the concept of the water splash but I don’t think it “flows” nicely together with the logo. Another thought is that maybe creating the logo out of water splash could work and have a dramatic effect (like the water text and the butterfly picture attached with similar background instead of white). If the above doesn’t work I would like to see a modern simplified design. One of the attached files named as the unwanted business card has all the details that I want included in the business card. Please note that it is two sided.
Updates

I am very thankful for the designs that I have received, but they are very similar and only a couple of attempts to do something with the water splash as per my original brief. Modernizing the logo and having it made out of out of water splash with the orange as color accent could work and have a dramatic effect (like the water text and the butterfly picture attached with similar background instead of white). Please do not use the butterfly itself! This is just an example that images can be created out of water splash.

Contact Information for Business Card

all the details are on the unwonted business card file included

Colors
3176b5

Requirements
Nice to have
• Copied from the brief:
• ... maybe creating the logo out of water splash could work and have a dramatic effect (like the water text and the butterfly picture attached with similar background instead of white). Please do not use the butterfly itself!
Should not have
• I am getting designs with a butterfly. The butterfly picture was an example of creating something from a water splash. The butterfly itself has no association with anything other than the concept of creating a logo out of water splash. Sorry, I thought I was clear in the brief.

```html
<!DOCTYPE html>
<html lang="en">
<head>
<meta charset="utf-8">
<title>Crestline Bathrooms – Business Card</title>
<link href="https://fonts.googleapis.com/css2?family=Roboto:wght@400;500&family=Schoolbell&display=swap" rel="stylesheet">
<style>
  :root {
    --page: #e6e6e6;
    --navy: #1a4c74;
    --ink: #151515;
    --body-grey: #555a5e;
    --accent: #e27a66;
    --badge-grey: #6a6a6a;
    --card-white: #ffffff;
  }
  * { margin: 0; padding: 0; box-sizing: border-box; }
  html, body { width: 1200px; height: 960px; overflow: hidden; }
  body {
    background: var(--page);
    font-family: "Roboto", Arial, sans-serif;
    position: relative;
  }
  .card {
    position: absolute;
    width: 600px;
    height: 344px;
    overflow: hidden;
  }
  /* Front */
  .card--front {
    left: 314px; top: 113px;
    background: linear-gradient(165deg, #6c8ea3 0%, #9dbccb 45%, #d6ebf2 80%, #e4f4f9 100%);
  }
  .splash-art {
    position: absolute;
    left: 200px; top: 0;
    width: 400px; height: 340px;
    background: radial-gradient(ellipse at 55% 50%, rgba(235,245,250,0.55) 0%, rgba(170,200,215,0.35) 40%, rgba(120,155,175,0) 72%);
  }
  .holder-name {
    position: absolute;
    left: 42px; top: 170px;
    font-family: "Schoolbell", "Comic Sans MS", cursive;
    font-size: 25px;
    color: var(--navy);
    letter-spacing: 0.5px;
  }
  .contact-list {
    position: absolute;
    left: 41px; top: 214px;
    list-style: none;
  }
  .contact-list li {
    display: flex;
    align-items: center;
    height: 19.5px;
    font-size: 14.5px;
    color: var(--ink);
  }
  .contact-list svg {
    width: 14px; height: 14px;
    margin-right: 9px;
    fill: var(--navy);
    flex: none;
  }
  /* Back */
  .card--back {
    left: 311px; top: 472px;
    background: var(--card-white);
  }
  .brand-name {
    position: absolute;
    left: 40px; top: 158px;
    width: 230px;
    display: flex;
    align-items: center;
    gap: 10px;
    font-size: 24px;
    font-weight: 500;
    color: var(--navy);
    white-space: nowrap;
  }
  .brand-dot {
    width: 14px; height: 14px;
    border-radius: 50%;
    background: var(--accent);
    flex: none;
  }
  .divider {
    position: absolute;
    left: 304px; top: 48px;
    width: 2px; height: 252px;
    background: var(--accent);
  }
  .service-list {
    position: absolute;
    left: 339px; top: 44px;
    list-style: none;
  }
  .service-list li {
    position: relative;
    padding-left: 16px;
    font-size: 14.5px;
    line-height: 19.5px;
    color: var(--body-grey);
    margin-bottom: 18px;
  }
  .service-list li::before {
    content: "";
    position: absolute;
    left: 0; top: 7px;
    width: 5px; height: 5px;
    border-radius: 50%;
    background: var(--navy);
  }
  .memberships {
    position: absolute;
    left: 339px; top: 265px;
    display: flex;
    align-items: center;
  }
  .badge-round {
    width: 32px; height: 34px;
    border-radius: 6px;
    background: var(--badge-grey);
  }
  .badge-rule {
    width: 1px; height: 34px;
    background: var(--badge-grey);
    margin: 0 18px;
  }
  .badge-wide {
    width: 118px; height: 28px;
    background: var(--badge-grey);
  }
</style>
</head>
<body>

<section class="card card--front">
  <div class="splash-art" role="img" aria-label="Sculptural water splash artwork on a soft blue background"></div>
  <h1 class="holder-name">Daniel Marsh</h1>
  <ul class="contact-list">
    <li>
      <svg viewBox="0 0 24 24"><path d="M6.6 10.8c1.4 2.8 3.8 5.1 6.6 6.6l2.2-2.2c.3-.3.7-.4 1-.2 1.1.4 2.3.6 3.6.6.6 0 1 .4 1 1V20c0 .6-.4 1-1 1C10.6 21 3 13.4 3 4c0-.6.4-1 1-1h3.5c.6 0 1 .4 1 1 0 1.3.2 2.5.6 3.6.1.3 0 .7-.2 1L6.6 10.8z"/></svg>
      0400 555 218
    </li>
    <li>
      <svg viewBox="0 0 24 24"><path d="M7 1h10c1.1 0 2 .9 2 2v18c0 1.1-.9 2-2 2H7c-1.1 0-2-.9-2-2V3c0-1.1.9-2 2-2zm0 3v14h10V4H7zm5 15.5a1.2 1.2 0 100 2.4 1.2 1.2 0 000-2.4z"/></svg>
      6200 4417
    </li>
    <li>
      <svg viewBox="0 0 24 24"><path d="M2 5h20v14H2V5zm2 2v.5l8 5 8-5V7H4zm0 2.8V17h16V9.8l-8 5-8-5z"/></svg>
      daniel@crestlinebathrooms.com.au
    </li>
    <li>
      <svg viewBox="0 0 24 24"><path d="M12 2a10 10 0 100 20 10 10 0 000-20zm-1 17.9A8 8 0 014.1 11H8c.2 1 .9 1.6 1.8 1.9l-.8 2.7 2 1.5v2.8zm6.9-2.5c-.3-.8-1-1.4-1.9-1.4h-1v-3c0-.6-.4-1-1-1H8v-2h2c.6 0 1-.4 1-1V7h2c1.1 0 2-.9 2-2v-.4a8 8 0 012.9 12.8z"/></svg>
      crestlinebathrooms.com.au
    </li>
    <li>
      <svg viewBox="0 0 24 24"><path d="M12 2a7 7 0 00-7 7c0 5.2 7 13 7 13s7-7.8 7-13a7 7 0 00-7-7zm0 9.5a2.5 2.5 0 110-5 2.5 2.5 0 010 5z"/></svg>
      PO Box 41, Karrabee 2600
    </li>
  </ul>
</section>

<section class="card card--back">
  <div class="brand-name"><span class="brand-dot"></span>Crestline Bathrooms</div>
  <div class="divider"></div>
  <ul class="service-list">
    <li>Complete Bathroom<br>Renovations &amp; Remodelling</li>
    <li>Highly Skilled &amp;<br>Qualified Tradespeople</li>
    <li>Professional Service From<br>Concept To Completion</li>
    <li>All Work Guaranteed</li>
  </ul>
  <div class="memberships">
    <div class="badge-round" role="img" aria-label="Industry association membership badge"></div>
    <div class="badge-rule"></div>
    <div class="badge-wide" role="img" aria-label="Builders association membership badge"></div>
  </div>
</section>

</body>
</html>
```